Dental specialist needs a sharp looking letterhead

I am looking for a letterhead to be used to send letters and communication between myself (a dental specialist) and other dentists.
My office is a state of the art dental specialty office.
I need to letterhead to also state:
Bertram L. Oswick DDS
2748 Tollard Avenue, Suite K
West Tollard, NY 14391
(716)392-5061
fax: (716)392-5087
oswickroot.com (**this email address may change)

i included my logo designs.
thank you

Target Market(s)

dentists

Industry/Entity Type

Communication

Requirements
Must have
• the included logo, whether the vertical or horizontal versions

```html
<!DOCTYPE html>
<html lang="en">
<head>
<meta charset="utf-8">
<title>Keystone Endodontics Letterhead</title>
<link href="https://fonts.googleapis.com/css2?family=Open+Sans:wght@400;600;700&display=swap" rel="stylesheet">
<style>
  :root {
    --backdrop: #9b9b9b;
    --paper: #ffffff;
    --brand-blue: #0ea5ec;
    --brand-green: #8cc63f;
    --ink: #3a3a3a;
    --ink-strong: #2b2b2b;
  }
  html, body {
    margin: 0;
    padding: 0;
    width: 1200px;
    height: 916px;
    overflow: hidden;
    background: var(--backdrop);
    font-family: "Open Sans", Arial, sans-serif;
  }
  .letterhead {
    position: absolute;
    left: 270px;
    top: 30px;
    width: 660px;
    height: 856px;
    background: var(--paper);
    box-shadow: 0 6px 18px rgba(0,0,0,0.25);
    color: var(--ink);
  }
  .masthead {
    position: absolute;
    top: 44px;
    left: 420px;
    width: 220px;
  }
  .practice-mark {
    display: flex;
    align-items: center;
    gap: 7px;
    margin-bottom: 10px;
  }
  .practice-mark__square {
    width: 22px;
    height: 22px;
    background: var(--brand-blue);
    flex: none;
  }
  .practice-mark__name {
    font-weight: 700;
    font-size: 11px;
    line-height: 1.15;
    color: var(--ink-strong);
    letter-spacing: 0.3px;
  }
  .doctor-name {
    font-size: 12px;
    color: var(--brand-blue);
    letter-spacing: 1.4px;
    margin: 0;
  }
  .doctor-credential {
    font-size: 10px;
    color: var(--brand-green);
    letter-spacing: 1px;
    margin: 2px 0 6px;
  }
  .contact-list {
    font-size: 8.5px;
    line-height: 1.45;
    margin: 0;
    color: var(--ink-strong);
  }
  .contact-list dt {
    display: inline;
    color: var(--brand-blue);
  }
  .contact-list dd {
    display: inline;
    margin: 0;
  }
  .contact-list .contact-row { display: block; }
  .contact-list .contact-indent { display: block; }
  .letter-body {
    position: absolute;
    top: 235px;
    left: 78px;
    width: 505px;
    font-size: 8.6px;
    line-height: 1.45;
  }
  .letter-body p { margin: 0 0 11px; }
  .letter-closing {
    position: absolute;
    top: 600px;
    left: 78px;
    font-size: 8.6px;
    margin: 0;
  }
  .footer-band {
    position: absolute;
    left: 0;
    right: 0;
    bottom: 0;
    height: 30px;
    background: var(--brand-blue);
    display: flex;
    align-items: center;
    justify-content: center;
  }
  .footer-band__site {
    color: #ffffff;
    font-size: 11px;
    letter-spacing: 4px;
  }
</style>
</head>
<body>
  <main class="letterhead">
    <header class="masthead">
      <div class="practice-mark">
        <span class="practice-mark__square"></span>
        <span class="practice-mark__name">KEYSTONE<br>ENDODONTICS P.C.</span>
      </div>
      <p class="doctor-name">Bertram L. Oswick</p>
      <p class="doctor-credential">D.D.S</p>
      <dl class="contact-list">
        <div class="contact-row"><dt>Address:</dt> <dd>2748 Tollard Avenue</dd></div>
        <div class="contact-indent"><dd>Suite K West Tollard, NY 14391</dd></div>
        <div class="contact-row"><dt>Phone:</dt> <dd>(716)392-5061</dd></div>
        <div class="contact-row"><dt>Fax:</dt> <dd>(716)392-5087</dd></div>
      </dl>
    </header>

    <section class="letter-body">
      <p>Lorem ipsum,</p>
      <p>Lorem ipsum dolor sit amet, consectetuer adipiscing elit. Nam cursus. Morbi ut mi. Nullam enim leo, egestas id, condimentum at, laoreet mattis, massa. Sed eleifend nonummy diam. Praesent mauris ante, elementum et, bibendum at, posuere sit amet, nibh. Duis tincidunt lectus quis dui viverra vestibulum. Suspendisse vulputate aliquam dui. Nulla elementum dui ut augue.</p>
      <p>Aliquam vehicula mi at mauris. Maecenas placerat, nisl at consequat rhoncus, sem nunc gravida justo, quis eleifend arcu velit quis lacus. Morbi magna magna, tincidunt a, mattis non, imperdiet vitae, tellus.</p>
      <p>Mauris nunc quam, venenatis nec, euismod sit amet, egestas placerat, est. Pellentesque habitant morbi tristique senectus et netus et malesuada fames ac turpis egestas. Cras id elit. Integer quis urna.</p>
      <p>Aliquam vehicula mi at mauris. Maecenas placerat, nisl at consequat rhoncus, sem nunc gravida justo, quis eleifend arcu velit quis lacus. Morbi magna magna, tincidunt a, mattis non, imperdiet vitae, tellus.</p>
      <p>Mauris nunc quam, venenatis nec, euismod sit amet, egestas placerat, est. Pellentesque habitant morbi tristique senectus et netus et malesuada fames ac turpis egestas. Cras id elit. Integer quis urna.</p>
    </section>

    <p class="letter-closing">Sincerly,</p>

    <footer class="footer-band">
      <span class="footer-band__site">www.oswickroot.com</span>
    </footer>
  </main>
</body>
</html>
```